Grey Fennel Medical Website to make connecting and communicating easier

To create a unique, user-friendly, professional website for patients and professionals to access education/ information, forms, appointments, contact details, and data about us, and for us to have the capacity to link to various cloud-based platforms.
To use the logo design and colour scheme we have just sourced.

WEBSITE to be eye catching, Inspiring and alluring
- efficient and logical
- professional and trustworthy appearance
- health focus "living health matters"
- user friendly
- ability to link with cloud-based software and video conferencing tools/ telehealth
- colours- black/ white teal and ?silver

PAGES:
page 1 - Our clinic and staff, services offered, contact us- address/ map / contact details- social media connections
page 2- patients and visitors - New patient forms to complete, news and patient informtion (educatinal)
page 3 - health professionals -referral forms, research and education
page 3- online appointments
page 4 - Quick links - partners, other services
page 5- privacy policy, disclaimer

HI, Could we please extend the deadline another 5 days, so sorry just struggling with my workload to be able to keep up and I am wanting to liaise more with the designer that I will choose. I am so happy with SketchHarbor and all the designers - thank you! Thank you so much!!

Target Market(s)

Patients - mostly over 60's so the website must be minimal clicks and simple to navigate
Professionals - for education and access forms

Industry/Entity Type

Health Care

Coding

Coded - Design and coding required

Number of Pages Required

5+ page

Font styles to use
Sans Serif
Script

Colors
33b8a4
86cfc6

Requirements
Must have
• WEBSITE to be eye catching, Inspiring and alluring
- efficient and logical
- user friendly

WEBSITE - professional and user friendly
- ability to link with cloud based software and videoconferencing/ telehealth
Nice to have
• clean and crisp presentation
happy for an innovative look
room to add more services and ability to link pages and resources
Should not have
• Please ensure the website is not:
clunky
difficult to navigate
common and cheap looking

```html
<!DOCTYPE html>
<html lang="en">
<head>
<meta charset="utf-8">
<title>Grey Fennel Medical</title>
<link href="https://fonts.googleapis.com/css2?family=Poppins:wght@300;400;500;600;700;800&display=swap" rel="stylesheet">
<style>
:root{
  --teal:#33b8a4;
  --teal-soft:#86cfc6;
  --teal-pale:#d6f0ec;
  --ink:#1b1b1b;
  --grey:#8a8a8a;
  --line:#e6e6e6;
  --band:#efefef;
  --dark:#161a19;
  --white:#ffffff;
}
*{box-sizing:border-box;margin:0;padding:0}
html,body{width:1200px;height:4728px;overflow:hidden}
body{font-family:'Poppins',sans-serif;color:var(--ink);background:var(--white);position:relative}
.abs{position:absolute}
.teal{color:var(--teal)}

/* header */
.topbar{top:0;left:0;width:1200px;height:64px;background:var(--white)}
.call-icon{left:60px;top:8px;width:48px;height:48px;border-radius:50%;background:#eef4f3;display:flex;align-items:center;justify-content:center}
.call-text{left:117px;top:12px;line-height:1.15}
.call-text small{display:block;font-size:13px;color:var(--teal);font-weight:500}
.call-text strong{font-size:18px;font-weight:600}
.btn-dark{left:936px;top:14px;width:202px;height:36px;border-radius:18px;background:var(--ink);color:#fff;font-size:12px;font-weight:600;display:flex;align-items:center;justify-content:center;letter-spacing:.3px}
.navbar{top:64px;left:0;width:1200px;height:41px;background:var(--teal)}
.nav-link{top:76px;color:#fff;font-size:11.5px;font-weight:600;letter-spacing:.2px}
.logo-cap{left:500px;top:0;width:200px;height:156px;background:#fff;border-radius:0 0 100px 100px;border:3px solid var(--teal-soft);border-top:none;text-align:center;padding-top:66px}
.logo-dot{position:absolute;left:84px;top:16px;width:32px;height:32px;border-radius:50%;border:3px solid var(--teal)}
.logo-name{font-size:17px;font-weight:600;color:var(--teal);line-height:1.3}

/* hero */
.hero{top:105px;left:0;width:1200px;height:620px;background:linear-gradient(160deg,#7d9a4c 0%,#a9bf6a 35%,#c9c38f 65%,#8aa25a 100%)}
.hero-title{left:62px;top:226px;font-size:59px;line-height:1.2;font-weight:800;color:#fff;letter-spacing:1.5px}
.hero-copy{left:62px;top:380px;font-size:12px;line-height:1.75;color:#fff}
.btn-teal{background:var(--teal);color:#fff;font-weight:600;display:flex;align-items:center;justify-content:center;border-radius:24px}

/* section titles */
.title{left:0;width:1200px;text-align:center;font-size:36px;font-weight:700;letter-spacing:.5px}

/* cards */
.svc{width:248px;height:259px;border:1px solid var(--line);background:#fff;text-align:center}
.svc .ph{margin:8px;height:142px}
.svc h3{font-size:15px;font-weight:500;margin-top:18px}
.svc p{font-size:10.5px;color:var(--grey);line-height:1.8;margin:8px 24px 0}
.pill{border-radius:18px;font-size:12px;font-weight:600;display:flex;align-items:center;justify-content:center}

/* about */
.about-text{left:601px;top:1750px;width:480px;font-size:12px;line-height:1.75;color:#fff}

/* staff */
.staff{width:248px;height:389px;border:1px solid var(--line);text-align:center}
.staff .ph{height:248px}
.staff h4{font-size:14px;font-weight:700;margin-top:24px}
.staff p{font-size:10.5px;color:var(--teal);margin-top:6px}
.soc{display:flex;justify-content:center;gap:12px;margin-top:18px}
.soc span{width:26px;height:26px;border-radius:50%;background:var(--teal-pale)}

/* testimonials */
.quote{width:526px;height:178px;background:#fff}
.quote .av{position:absolute;left:22px;top:24px;width:74px;height:74px;border-radius:50%}
.quote h5{position:absolute;left:114px;top:38px;font-size:15px;font-weight:600}
.quote small{position:absolute;left:114px;top:62px;font-size:10.5px;color:var(--teal)}
.quote .mark{position:absolute;right:22px;top:-2px;font-size:100px;font-weight:800;color:var(--teal-soft);line-height:1;opacity:.8}
.quote p{position:absolute;left:28px;top:110px;right:28px;font-size:12px;line-height:1.8;color:#666}
.dots{top:3193px;left:0;width:1200px;display:flex;justify-content:center;gap:8px}
.dots span{width:8px;height:8px;border-radius:50%;background:#d6d6d6}
.dots span:first-child{background:var(--teal)}

/* blog */
.post{width:338px;height:404px;background:#f2f2f2}
.post .ph{height:218px;position:relative}
.post .date{position:absolute;left:0;bottom:0;width:130px;height:32px;background:var(--teal);color:#fff;font-size:11px;padding:8px 0 0 14px}
.post h6{font-size:12px;font-weight:600;margin:26px 14px 0}
.post p{font-size:11.5px;line-height:1.85;color:#666;margin:10px 14px 0}
.post a{display:block;margin:8px 14px 0;font-size:11px;font-weight:600;color:var(--teal);text-decoration:none}

/* contact */
.contact{top:3945px;left:0;width:1200px;height:643px;background:linear-gradient(120deg,#1f2523 0%,#121514 50%,#1e2a25 100%)}
.c-icon{left:60px;width:76px;height:76px;border-radius:50%;background:#fff;display:flex;align-items:center;justify-content:center}
.c-text{left:152px;color:#fff;line-height:1.5}
.c-text small{display:block;font-size:14px;color:var(--teal)}
.c-text strong{font-size:15px;font-weight:600}
.form{left:690px;top:4169px;width:352px;height:327px;background:var(--teal);padding:28px 20px}
.form h5{color:#fff;font-size:12px;font-weight:600;margin-bottom:16px}
.field{height:32px;background:#a7ded6;border-radius:2px;font-size:10px;color:#2a5f58;padding:9px 8px;margin-bottom:10px}
.field.big{height:70px}
.form .send{width:158px;height:36px;background:#fff;color:var(--teal);font-size:12px;margin-top:12px}

/* footer */
.f-links{top:4681px;right:60px;display:flex;gap:20px;font-size:11px;color:var(--grey)}
.f-links span:first-child{color:var(--teal)}
.f-soc{top:4649px;right:60px;display:flex;gap:20px}
.f-soc span{width:12px;height:12px;border-radius:50%;background:var(--teal)}
</style>
</head>
<body>

<!-- Hero -->
<div class="abs hero" role="img" aria-label="Photo of a woman and a man jogging on a sunlit grassy park path"></div>
<svg class="abs" style="left:0;top:560px" width="1200" height="170" viewBox="0 0 1200 170" aria-hidden="true">
  <path d="M0 90 C180 20 330 10 520 80 C700 145 900 150 1200 40 L1200 170 L0 170 Z" fill="#fff"/>
  <path d="M0 100 C180 40 330 40 520 110 C700 170 900 165 1200 70" fill="none" stroke="#bfe6e0" stroke-width="8"/>
  <path d="M0 90 C180 20 330 10 520 80 C700 145 900 150 1200 40" fill="none" stroke="#fff" stroke-width="2"/>
</svg>
<h1 class="abs hero-title">LIVING HEALTH<br>MATTERS</h1>
<p class="abs hero-copy">Lorem Ipsum is simply dummy text of the printing and typesetting industry.<br>Lorem Ipsum has been the industry's standard dummy text.</p>
<div class="abs btn-teal" style="left:60px;top:440px;width:225px;height:44px;font-size:13px">GET APPOINTMENT</div>

<!-- Header -->
<div class="abs topbar"></div>
<div class="abs call-icon">
  <svg width="22" height="22" viewBox="0 0 24 24"><path d="M6.6 10.8a15 15 0 0 0 6.6 6.6l2.2-2.2c.3-.3.7-.4 1-.2 1.1.4 2.3.6 3.6.6.6 0 1 .4 1 1V20c0 .6-.4 1-1 1A17 17 0 0 1 3 4c0-.6.4-1 1-1h3.5c.6 0 1 .4 1 1 0 1.3.2 2.5.6 3.6.1.3 0 .7-.2 1z" fill="none" stroke="#1b1b1b" stroke-width="1.6"/></svg>
</div>
<div class="abs call-text"><small>CALL US</small><strong>123 456 7890</strong></div>
<div class="abs btn-dark">GET AN APPOINTMENT</div>
<div class="abs navbar"></div>
<span class="abs nav-link" style="left:61px">HOME</span>
<span class="abs nav-link" style="left:131px">ABOUT US</span>
<span class="abs nav-link" style="left:226px">OUR SERVICES</span>
<span class="abs nav-link" style="left:345px">NEW PATIENTS</span>
<span class="abs nav-link" style="left:711px">HEALTH PROFESSIONAL</span>
<span class="abs nav-link" style="left:891px">ONLINE APPOINTMENT</span>
<span class="abs nav-link" style="left:1059px">CONTACT US</span>
<div class="abs logo-cap"><span class="logo-dot"></span><div class="logo-name">GREY FENNEL<br>MEDICAL</div></div>

<!-- Services -->
<h2 class="abs title" style="top:772px">OUR <span class="teal">SERVICES</span></h2>
<div class="abs svc" style="left:60px;top:855px"><div class="ph" role="img" aria-label="Doctor consulting a patient" style="background:linear-gradient(135deg,#dfe6ea,#b9c7cf)"></div><h3>General Practice</h3><p>Lorem ipsum has been the industry's standard dummy text.</p></div>
<div class="abs svc" style="left:337px;top:855px"><div class="ph" role="img" aria-label="Medical staff in protective suits treating a patient" style="background:linear-gradient(135deg,#7fa3a6,#3f6a70)"></div><h3>Covid-19 Service</h3><p>Lorem ipsum has been the industry's standard dummy text.</p></div>
<div class="abs svc" style="left:614px;top:855px"><div class="ph" role="img" aria-label="Pharmacist at medicine shelves" style="background:linear-gradient(135deg,#e8e2d6,#b8b0a0)"></div><h3>Pharmacy</h3><p>Lorem ipsum has been the industry's standard dummy text.</p></div>
<div class="abs svc" style="left:891px;top:855px"><div class="ph" role="img" aria-label="Smiling woman with healthy teeth" style="background:linear-gradient(135deg,#5a3a2a,#c59a80)"></div><h3>Dentists</h3><p>Lorem ipsum has been the industry's standard dummy text.</p></div>
<div class="abs svc" style="left:60px;top:1149px"><div class="ph" role="img" aria-label="Woman doing an exercise lunge" style="background:linear-gradient(135deg,#d8d8d6,#a8a8a4)"></div><h3>Phisiotherapy</h3><p>Lorem ipsum has been the industry's standard dummy text.</p></div>
<div class="abs svc" style="left:337px;top:1149px"><div class="ph" role="img" aria-label="Dermatologist examining a patient's back" style="background:linear-gradient(135deg,#efe6df,#cdb3a2)"></div><h3>Dermatology</h3><p>Lorem ipsum has been the industry's standard dummy text.</p></div>
<div class="abs svc" style="left:614px;top:1149px"><div class="ph" role="img" aria-label="Hands massaging a foot" style="background:linear-gradient(135deg,#f1c7b0,#e08e70)"></div><h3>Podiatry</h3><p>Lorem ipsum has been the industry's standard dummy text.</p></div>
<div class="abs svc" style="left:891px;top:1149px"><div class="ph" role="img" aria-label="Chiropractor treating a patient's spine" style="background:linear-gradient(135deg,#f0d2c0,#e07a4a)"></div><h3>Chriopractic</h3><p>Lorem ipsum has been the industry's standard dummy text.</p></div>
<div class="abs pill" style="left:536px;top:1442px;width:128px;height:35px;background:var(--teal);color:#fff">VIEW MORE</div>

<!-- About -->
<svg class="abs" style="left:0;top:1530px" width="1200" height="580" viewBox="0 0 1200 580" aria-hidden="true">
  <path d="M0 50 C200 110 380 110 600 50 C820 -10 1000 -5 1200 40 L1200 520 C1000 460 800 470 600 520 C400 570 200 575 0 570 Z" fill="#33b8a4"/>
</svg>
<div class="abs" style="left:61px;top:1579px;width:410px;height:410px;border-radius:50%;background:#fff"></div>
<div class="abs" role="img" aria-label="Smiling couple embracing outdoors" style="left:69px;top:1587px;width:394px;height:394px;border-radius:50%;background:linear-gradient(135deg,#e9d6b6,#b89678 60%,#7a8a70)"></div>
<h2 class="abs" style="left:601px;top:1690px;font-size:36px;font-weight:700;color:#fff">ABOUT US</h2>
<p class="abs about-text">Lorem Ipsum is simply dummy text of the printing and typesetting industry. Lorem Ipsum has been the industry's standard dummy text ever since the 1500s, when an unknown printer took a galley of type and scrambled it to make a type specimen book.Lorem Ipsum is simply dummy text of the printing and typesetting industry. Lorem Ipsum has been the industry.Lorem Ipsum is simply dummy text of the printing and typesetting industry. Lorem Ipsum has been the industry's standard dummy text ever since the 1500s, when an unknown printer took a galley of type and scrambled it to make a type specimen book.Lorem Ipsum is simply dummy text of the printing and typesetting industry. Lorem ipsum has been the industry.</p>
<div class="abs pill" style="left:601px;top:1989px;width:126px;height:35px;background:#fff;color:var(--ink)">VIEW MORE</div>

<!-- Staff -->
<h2 class="abs title" style="top:2210px">MEET <span class="teal">OUR STAFF</span></h2>
<div class="abs staff" style="left:60px;top:2286px"><div class="ph" role="img" aria-label="Portrait of a female specialist" style="background:linear-gradient(135deg,#f2ece6,#c9b8a8)"></div><h4>SPECIALIST NAME</h4><p>Lorem ipsum is simply dummy text</p><div class="soc"><span></span><span></span></div></div>
<div class="abs staff" style="left:337px;top:2286px"><div class="ph" role="img" aria-label="Portrait of a male doctor wearing a mask" style="background:linear-gradient(135deg,#e6e6e6,#9fb2b0)"></div><h4>SPECIALIST NAME</h4><p>Lorem ipsum is simply dummy text</p><div class="soc"><span></span><span></span></div></div>
<div class="abs staff" style="left:614px;top:2286px"><div class="ph" role="img" aria-label="Portrait of a female doctor outdoors" style="background:linear-gradient(135deg,#5e7a44,#c2c8b4)"></div><h4>SPECIALIST NAME</h4><p>Lorem ipsum is simply dummy text</p><div class="soc"><span></span><span></span></div></div>
<div class="abs staff" style="left:891px;top:2286px"><div class="ph" role="img" aria-label="Portrait of a male specialist on pink background" style="background:linear-gradient(135deg,#e06a8c,#d24f78)"></div><h4>SPECIALIST NAME</h4><p>Lorem ipsum is simply dummy text</p><div class="soc"><span></span><span></span></div></div>

<!-- Testimonials -->
<svg class="abs" style="left:0;top:2760px" width="1200" height="570" viewBox="0 0 1200 570" aria-hidden="true">
  <path d="M0 60 C250 110 450 100 700 60 C900 25 1050 0 1200 20 L1200 500 C1000 470 850 540 600 550 C350 560 150 510 0 540 Z" fill="#efefef"/>
</svg>
<h2 class="abs title" style="top:2898px">WHAT <span class="teal">CLIENT SAY</span></h2>
<div class="abs quote" style="left:60px;top:2991px"><div class="av" role="img" aria-label="Patient portrait" style="background:linear-gradient(135deg,#e8cfb2,#b88f6a)"></div><h5>Patient Name</h5><small>Lorem ipsum is dummy text</small><div class="mark">”</div><p>Lorem Ipsum is dummy text of the printing and typesetting industry. Lorem Ipsum has been the industry's standard dummy text ever since the 1500.</p></div>
<div class="abs quote" style="left:614px;top:2991px"><div class="av" role="img" aria-label="Patient portrait" style="background:linear-gradient(135deg,#d8d8d8,#8a7a6c)"></div><h5>Patient Name</h5><small>Lorem ipsum is dummy text</small><div class="mark">”</div><p>Lorem Ipsum is dummy text of the printing and typesetting industry. Lorem Ipsum has been the industry's standard dummy text ever since the 1500.</p></div>
<div class="abs dots"><span></span><span></span><span></span><span></span><span></span></div>

<!-- Blog -->
<h2 class="abs title" style="top:3395px">LATEST <span class="teal">BLOG</span></h2>
<div class="abs post" style="left:60px;top:3468px"><div class="ph" role="img" aria-label="Nurse examining a patient" style="background:linear-gradient(135deg,#8fb6d6,#e8d5c6)"><div class="date">10 Nov 2020</div></div><h6>Lorem Ipsum is dummy text of the printing.</h6><p>Lorem Ipsum is simply dummy text of the printing and typesetting industry. Lorem Ipsum has been the industry's standard dummy text ever since the 1500.</p><a>READ MORE &rarr;</a></div>
<div class="abs post" style="left:431px;top:3468px"><div class="ph" role="img" aria-label="Medical worker in protective suit with virus imagery" style="background:linear-gradient(135deg,#1e3f7a,#4f8fc8)"><div class="date">10 Nov 2020</div></div><h6>Lorem Ipsum is dummy text of the printing.</h6><p>Lorem Ipsum is simply dummy text of the printing and typesetting industry. Lorem Ipsum has been the industry's standard dummy text ever since the 1500.</p><a>READ MORE &rarr;</a></div>
<div class="abs post" style="left:802px;top:3468px"><div class="ph" role="img" aria-label="Woman jogging at sunset" style="background:linear-gradient(135deg,#c9a25a,#6d6a4a)"><div class="date">10 Nov 2020</div></div><h6>Lorem Ipsum is dummy text of the printing.</h6><p>Lorem Ipsum is simply dummy text of the printing and typesetting industry. Lorem Ipsum has been the industry's standard dummy text ever since the 1500.</p><a>READ MORE &rarr;</a></div>

<!-- Contact -->
<div class="abs contact" role="img" aria-label="Dark background photo of a doctor with a plant"></div>
<svg class="abs" style="left:0;top:3930px" width="1200" height="80" viewBox="0 0 1200 80" aria-hidden="true">
  <path d="M0 0 L1200 0 L1200 20 C950 70 700 10 450 40 C250 65 100 40 0 60 Z" fill="#fff"/>
</svg>
<svg class="abs" style="left:0;top:4500px" width="1200" height="228" viewBox="0 0 1200 228" aria-hidden="true">
  <path d="M0 20 C250 90 500 110 760 80 C950 60 1100 30 1200 40 L1200 228 L0 228 Z" fill="#f4f4f4"/>
</svg>
<h2 class="abs title" style="top:4090px;color:#fff">CONTACT US</h2>
<div class="abs c-icon" style="top:4152px"><svg width="30" height="30" viewBox="0 0 24 24"><path d="M6.6 10.8a15 15 0 0 0 6.6 6.6l2.2-2.2c.3-.3.7-.4 1-.2 1.1.4 2.3.6 3.6.6.6 0 1 .4 1 1V20c0 .6-.4 1-1 1A17 17 0 0 1 3 4c0-.6.4-1 1-1h3.5c.6 0 1 .4 1 1 0 1.3.2 2.5.6 3.6.1.3 0 .7-.2 1z" fill="none" stroke="#33b8a4" stroke-width="1.4"/></svg></div>
<div class="abs c-text" style="top:4163px"><small>Call Us</small><strong style="font-size:18px">123 456 7890</strong></div>
<div class="abs c-icon" style="top:4275px"><svg width="30" height="30" viewBox="0 0 24 24"><rect x="3" y="5" width="18" height="14" rx="1" fill="none" stroke="#33b8a4" stroke-width="1.4"/><path d="M3 6l9 7 9-7" fill="none" stroke="#33b8a4" stroke-width="1.4"/></svg></div>
<div class="abs c-text" style="top:4290px"><small>Email Us</small><strong style="font-size:12px">info@greyfennelmedical.com</strong></div>
<div class="abs c-icon" style="top:4395px"><svg width="30" height="30" viewBox="0 0 24 24"><path d="M12 22s7-7 7-12a7 7 0 0 0-14 0c0 5 7 12 7 12z" fill="none" stroke="#33b8a4" stroke-width="1.4"/><circle cx="12" cy="10" r="2.5" fill="none" stroke="#33b8a4" stroke-width="1.4"/></svg></div>
<div class="abs c-text" style="top:4410px"><small>Address</small><span style="font-size:12px">Lorem ipsum is simply dummy text</span></div>
<div class="abs form">
  <h5>Send Us A Message</h5>
  <div class="field">Name</div>
  <div class="field">Email</div>
  <div class="field">Contact No.</div>
  <div class="field big">Message</div>
  <div class="pill send">SEND MESSAGE</div>
</div>

<!-- Footer -->
<div class="abs" style="left:118px;top:4578px;width:30px;height:30px;border-radius:50%;border:3px solid var(--teal)"></div>
<div class="abs" style="left:60px;top:4617px;font-size:17px;font-weight:600;color:var(--teal);line-height:1.3;text-align:center">GREY FENNEL<br>MEDICAL</div>
<div class="abs f-soc"><span></span><span></span><span></span><span></span><span></span></div>
<div class="abs f-links"><span>Home</span><span>About Us</span><span>Our Services</span><span>New Patients</span><span>Health Professional</span><span>Online Appointment</span><span>Contact</span></div>

</body>
</html>
```